Emerging automotive detailing business

I am starting a small automotive detailing business in hopes of becoming a well-known detailer to work on high end cars. I would like a card to reflect the high quality and time I put into my work. The name of the company is Bright Crest Detailing. I feel like it represents racecars getting off the line at the drag strip as well as an innuendo of "Up the Ladder". I do minor paint correction such as clay barring, multi-step buffing and polishing, waxing, hand washes, etc. I am always striving to learn more and improve my work. My goal is to have total customer satisfaction. This is a female run business but I do not want it to be very girly. Elegant is okay! I have pictures of my personal wrenfield attached, they do not need to be incorporated but if you can think of a cool way to use 1 or all of them, go for it!

Target Market(s)

Anyone that owns a vehicle. Preferably high end vehicles such as Valtori, Castellverde and Morvani but I will also happily work on any car, truck or suv no matter what brand.

Industry/Entity Type

Automotive

Contact Information for Business Card

Bright Crest Detailing
Mira Tolland
4175 Quenhollow Rd
Ashmere PA 17492
Cell phone- call/text- 717-555-0148
email- brightcrestdetails@maildrop-example.com
Instagram: @brightcrestdetailing
Facebook: facebook.com/brightcrestdetailing

Requirements
Must have
• Business name, my name, address, phone number. Listing that I do minor paint correction such as clay barring, multi-step buffing and polishing, waxing, hand washes, interior cleaning, and more. (This last part was in nice to haves but I have realized that I do really want it, so I moved it to must haves.) I want something that is different and eye-catching to my customers. Some people have done this very well with cards already submitted to me, but a lot have not. I didn't mess with the "look and feel bars" much because because I am pretty open to the overall design as long as it is not your basic run of the mill design.
Nice to have
• Something car related. Maybe an appointment time/date line. I do not have a logo, but if you would like to design one and incorporate it, that would be amazing!
Should not have
• Purple and Pink colors. Boring, basic, normal card.

```html
<!DOCTYPE html>
<html lang="en">
<head>
<meta charset="utf-8">
<title>Bright Crest Detailing — Business Card</title>
<link rel="stylesheet" href="https://fonts.googleapis.com/css2?family=Tinos&family=Arimo:ital,wght@0,400;1,400&display=swap">
<style>
  :root {
    --page: #e9e7e3;
    --card-white: #f4f4f3;
    --band-dark: #3b4245;
    --band-text: #eef1f2;
    --sky-top: #29c6e6;
    --sky-bottom: #07b3e8;
    --panel: #f3f3f2;
    --panel-edge: #8a8f4c;
    --ink: #1d1f21;
    --ink-soft: #2c2f31;
    --ink-muted: #4a5053;
    --icon: #1f2426;
  }
  * { box-sizing: border-box; margin: 0; padding: 0; }
  html, body { width: 1200px; height: 892px; overflow: hidden; }
  body {
    background: var(--page);
    display: flex;
    align-items: center;
    justify-content: center;
    gap: 44px;
    font-family: "Arimo", Arial, sans-serif;
  }
  .card {
    width: 540px;
    height: 309px;
    position: relative;
    overflow: hidden;
    border-radius: 4px;
    box-shadow: 0 6px 18px rgba(0,0,0,.18);
  }

  /* Side one: white with dark contact band */
  .card--classic { background: var(--card-white); }
  .classic-title {
    position: absolute;
    top: 52px; left: 0; right: 0;
    text-align: center;
    font-family: "Tinos", "Times New Roman", serif;
    font-weight: 400;
    font-size: 34px;
    letter-spacing: .5px;
    color: var(--ink);
  }
  .classic-name {
    position: absolute;
    top: 98px; left: 0; right: 0;
    text-align: center;
    font-size: 22px;
    font-weight: 400;
    color: var(--ink-soft);
  }
  .service-list {
    position: absolute;
    top: 142px; left: 40px; right: 40px;
    list-style: none;
    display: flex;
    flex-wrap: wrap;
    justify-content: center;
    gap: 4px 0;
    font-size: 12px;
    color: var(--ink-muted);
  }
  .service-list li { white-space: nowrap; }
  .service-list li + li::before {
    content: "";
    display: inline-block;
    width: 4px; height: 4px;
    margin: 0 8px 2px;
    background: var(--sky-bottom);
  }
  .accent-rule {
    position: absolute;
    left: 0; right: 0; bottom: 104px;
    height: 4px;
    background: linear-gradient(90deg, var(--sky-top), var(--sky-bottom));
  }
  .classic-band {
    position: absolute;
    left: 0; right: 0; bottom: 0;
    height: 104px;
    background: var(--band-dark);
    display: flex;
    align-items: center;
    justify-content: space-between;
    padding: 0 18px 8px;
    color: var(--band-text);
    font-size: 14px;
  }
  .classic-band .phone { font-style: italic; }
  .classic-band .email { font-size: 12px; }

  /* Side two: sky blue with white name panel */
  .card--sky {
    background: linear-gradient(160deg, var(--sky-top) 0%, var(--sky-bottom) 100%);
  }
  .name-panel {
    position: absolute;
    top: 30px; left: 0;
    width: 360px; height: 96px;
    background: var(--panel);
    border: 1.5px solid var(--panel-edge);
    border-left: none;
    border-radius: 0 14px 14px 0;
    padding: 18px 0 0 56px;
  }
  .panel-title {
    font-size: 25px;
    font-weight: 400;
    color: var(--ink);
    letter-spacing: .2px;
  }
  .panel-name {
    margin-top: 4px;
    margin-left: 28px;
    font-size: 19px;
    color: var(--ink-soft);
  }
  .contact-list {
    position: absolute;
    top: 146px; left: 80px;
    list-style: none;
    font-size: 14px;
    color: var(--ink);
  }
  .contact-list li {
    display: flex;
    align-items: center;
    gap: 8px;
    height: 22px;
  }
  .contact-list li.email { font-size: 12.5px; }
  .contact-icon { width: 11px; height: 11px; flex: none; }
  .appointment {
    position: absolute;
    left: 80px; bottom: 26px;
    display: flex;
    gap: 18px;
    font-size: 12px;
    color: var(--ink);
  }
  .appointment span {
    display: inline-block;
    border-bottom: 1px solid var(--ink);
    padding-bottom: 2px;
  }
  .appointment .date { width: 170px; }
  .appointment .time { width: 110px; }
</style>
</head>
<body>

  <section class="card card--classic" aria-label="Business card, white side">
    <h1 class="classic-title">Bright Crest Detailing</h1>
    <p class="classic-name">Mira Tolland</p>
    <ul class="service-list" aria-label="Services">
      <li>Minor paint correction</li>
      <li>Clay barring</li>
      <li>Multi-step buffing &amp; polishing</li>
      <li>Waxing</li>
      <li>Hand washes</li>
      <li>Interior cleaning &amp; more</li>
    </ul>
    <div class="accent-rule"></div>
    <div class="classic-band">
      <span class="phone">717-555-0148</span>
      <span class="handle">@brightcrestdetailing</span>
      <span class="email">brightcrestdetails@maildrop-example.com</span>
    </div>
  </section>

  <section class="card card--sky" aria-label="Business card, blue side">
    <div class="name-panel">
      <h2 class="panel-title">Bright Crest Detailing</h2>
      <p class="panel-name">Mira Tolland</p>
    </div>
    <ul class="contact-list">
      <li>
        <svg class="contact-icon" viewBox="0 0 12 12" aria-hidden="true">
          <rect width="12" height="12" fill="var(--icon)"/>
          <path d="M3.2 2.6 L4.8 2.6 L5.3 4.6 L4.4 5.3 Q5.2 6.9 6.7 7.6 L7.4 6.7 L9.4 7.2 L9.4 8.8 Q5.8 9.2 3 5.2 Q2.8 3.8 3.2 2.6Z" fill="#fff"/>
        </svg>
        <span>717-555-0148</span>
      </li>
      <li>
        <svg class="contact-icon" viewBox="0 0 12 12" aria-hidden="true">
          <rect width="12" height="12" fill="var(--icon)"/>
        </svg>
        <span>@brightcrestdetailing</span>
      </li>
      <li class="email">
        <svg class="contact-icon" viewBox="0 0 12 12" aria-hidden="true">
          <rect width="12" height="12" fill="var(--icon)"/>
          <rect x="2.2" y="3.4" width="7.6" height="5.2" fill="none" stroke="#fff" stroke-width="1"/>
          <path d="M2.2 3.4 L6 6.4 L9.8 3.4" fill="none" stroke="#fff" stroke-width="1"/>
        </svg>
        <span>brightcrestdetails@maildrop-example.com</span>
      </li>
      <li>
        <svg class="contact-icon" viewBox="0 0 12 12" aria-hidden="true">
          <rect width="12" height="12" fill="var(--icon)"/>
          <path d="M6 2 A2.6 2.6 0 0 1 8.6 4.6 Q8.6 6.4 6 10 Q3.4 6.4 3.4 4.6 A2.6 2.6 0 0 1 6 2Z" fill="#fff"/>
          <circle cx="6" cy="4.6" r="1" fill="var(--icon)"/>
        </svg>
        <span>4175 Quenhollow Rd, Ashmere PA 17492</span>
      </li>
    </ul>
    <div class="appointment" aria-label="Appointment">
      <span class="date">Appointment:</span>
      <span class="time">Time:</span>
    </div>
  </section>

</body>
</html>
```